BRIVAN 2026 Flyer for Conference

BRIVAN needs a design for a 1-page flyer that we will hand out at an upcoming event & then later post online as a pdf. There are 3 elements which need to be on the flyer:

1) A logo. This should be prominent on the design (e.g., in the middle). The flyer should use the colors that are in that logo (e.g., for accents, design elements, and/or text; not all of these have to be used):
Dark blue: #185577
Med blue: #327C9A
Teal: #4EB1C2
Light Teal: #9EDBE6

2) The conference theme -- Oceans of Knowledge: Diving into Information Literacy -- should be at the flyer's top.

3) Finally, these six tracks should be listed below the theme and the logo (it's font size should be at least a couple sizes smaller than the size used for the theme):
- Pearls of Pedagogy: Teaching Techniques that Work
- The Depth Gauge: Measuring Instructional Impact
- Techtonic Shifts: Innovation and Educational Technology
- Captain's Log: Navigating Leadership in Library Instruction
- Swimming Together: Collaborating with Others
- The Bermuda Triangle: Exploring (Seemingly) Eternal Challenges

Font styles to use
Sans Serif

Colors
0094D4
00A9DD
6FCCEA
C7EBF8
E9F6FB

Requirements
Must have
• The 3 elements listed in the description: 1) the logo, 2) the text of the theme and 3) the text for the tracks.

```html
<!DOCTYPE html>
<html lang="en">
<head>
<meta charset="utf-8">
<title>BRIVAN 2026 – Oceans of Knowledge</title>
<link rel="stylesheet" href="https://fonts.googleapis.com/css2?family=Lexend:wght@500;600&family=Outfit:wght@500&display=swap">
<style>
  :root {
    --dark-blue: #185577;
    --med-blue: #327C9A;
    --teal: #4EB1C2;
    --light-teal: #9EDBE6;
    --ink: #2a2a2a;
    --black: #000000;
    --sand: #f2d6bf;
  }
  html, body { margin: 0; padding: 0; overflow: hidden; }
  body { width: 927px; height: 1200px; }
  .flyer {
    position: relative;
    width: 927px;
    height: 1200px;
    overflow: hidden;
    background: linear-gradient(180deg, #f3f3f3 0%, #f7f7f7 60%, #ececec 100%);
    font-family: "Lexend", "Helvetica Neue", Arial, sans-serif;
  }
  .shore-photo {
    position: absolute;
    left: 0; top: 0;
    width: 927px; height: 600px;
    background: linear-gradient(160deg, #f6dec9 0%, var(--sand) 45%, #c9d6bf 62%, #58c4cf 78%, #22b7cf 100%);
    clip-path: path("M0,0 H927 V592 C720,592 560,545 455,470 L0,470 Z");
  }
  .wave-art { position: absolute; left: 0; top: 0; }
  .brand {
    position: absolute;
    top: 62px; left: 0; width: 927px;
    text-align: center;
    margin: 0;
    font-weight: 600;
    font-size: 50px;
    letter-spacing: 1px;
    color: var(--dark-blue);
  }
  .theme {
    position: absolute;
    left: 61px; top: 251px;
    margin: 0;
    font-family: "Outfit", "Helvetica Neue", Arial, sans-serif;
    font-weight: 500;
    font-size: 47px;
    line-height: 73px;
    letter-spacing: -0.3px;
    color: #fff;
  }
  .theme .theme-lead { color: var(--light-teal); }
  .track {
    position: absolute;
    width: 410px;
  }
  .track-icon {
    position: absolute;
    left: 0; top: 14px;
    width: 60px; height: 60px;
    border-radius: 10px;
    background: linear-gradient(135deg, var(--light-teal), var(--teal));
    opacity: .55;
  }
  .track-title {
    position: absolute;
    left: 83px; top: 0;
    margin: 0;
    width: 330px;
    font-weight: 500;
    font-size: 21px;
    line-height: 44px;
    color: var(--ink);
    text-transform: uppercase;
    white-space: nowrap;
  }
  .col-left { left: 54px; }
  .col-right { left: 508px; }
  .base-band {
    position: absolute;
    left: 0; bottom: 0;
    width: 927px; height: 7px;
    background: var(--dark-blue);
  }
</style>
</head>
<body>
<main class="flyer">
  <div class="shore-photo" role="img" aria-label="Photograph of sandy beach with turquoise ocean waves washing ashore"></div>

  <svg class="wave-art" width="927" height="1200" viewBox="0 0 927 1200" aria-hidden="true">
    <path fill="var(--teal)" d="M370,220 C440,330 520,410 620,420 C720,428 840,400 927,370 L927,592 C720,592 560,545 455,470 Z"/>
    <path fill="var(--dark-blue)" d="M370,220 C440,330 520,410 620,420 C720,428 840,400 927,370 L927,555 C760,560 600,530 490,450 Z"/>
    <circle cx="211" cy="412" r="259" fill="var(--dark-blue)"/>
    <circle cx="211" cy="428" r="253" fill="var(--black)"/>
  </svg>

  <h2 class="brand">BRIVAN 2026</h2>

  <h1 class="theme">
    <span class="theme-lead">OCEANS OF<br>KNOWLEDGE:</span><br>
    DIVING INTO<br>INFORMATION<br>LITERACY
  </h1>

  <section class="track col-left" style="top:710px">
    <div class="track-icon" role="img" aria-label="Line icon of an open shell with a pearl"></div>
    <p class="track-title">Pearls of Pedagogy:<br>Teaching Techniques<br>That Work</p>
  </section>

  <section class="track col-left" style="top:865px">
    <div class="track-icon" role="img" aria-label="Line icon of stacked layers"></div>
    <p class="track-title">The Depth Gauge:<br>Measuring<br>Instructional Impact</p>
  </section>

  <section class="track col-left" style="top:1018px">
    <div class="track-icon" role="img" aria-label="Line icon of a schedule board with a clock"></div>
    <p class="track-title">Techtonic Shifts:<br>Innovation &amp;<br>Educational Technology</p>
  </section>

  <section class="track col-right" style="top:711px">
    <div class="track-icon" role="img" aria-label="Line icon of two people climbing steps toward a flag"></div>
    <p class="track-title">Captain's Log:<br>Navigating Leadership<br>in Library Instruction</p>
  </section>

  <section class="track col-right" style="top:868px">
    <div class="track-icon" role="img" aria-label="Line icon of a swimmer in waves"></div>
    <p class="track-title">Swimming Together:<br>Collaborating with<br>Others</p>
  </section>

  <section class="track col-right" style="top:1020px">
    <div class="track-icon" role="img" aria-label="Line icon of overlapping triangles"></div>
    <p class="track-title">The Bermuda Triangle:<br>Exploring (Seemingly)<br>Eternal Challenges</p>
  </section>

  <div class="base-band"></div>
</main>
</body>
</html>
```